Brookvane Consulting Business Card Design

Business Card Design for Brookvane Consulting. Brookvane Consulting is a boutique consultancy based in Atlanta, GA., that specializes in marketing strategy, organization planning, and leadership development. We provide solutions for small businesses and startups as well as Vantage 300 companies.

http://brookvaneconsulting.com/

Target Market(s)

We provide solutions for small businesses and startups as well as Vantage 300 companies.

Industry/Entity Type

Consulting

Contact Information for Business Card

Two sided business card with priority on contact information, logo, tag line (Inspiration to Dream More, Do More, Become More)

Colors

Designer to choose colors to be used in the design.

Requirements
Must have
• contact information, logo, tag line (Inspiration to Dream More, Do More, Become More)
• Simple no over communication.
Nice to have
• I would like to see different placements of logo and creative use of both sides of the card
Should not have
• Do not put too much information on the card.

```html
<!DOCTYPE html>
<html lang="en">
<head>
<meta charset="utf-8">
<title>Brookvane Consulting Business Card</title>
<link rel="stylesheet" href="https://fonts.googleapis.com/css2?family=Bebas+Neue&family=Lato:wght@300;400&display=swap">
<style>
  :root {
    --stage: #2b2b2b;
    --card-light: #f7f7f7;
    --card-light-edge: #e6e6e6;
    --card-dark: #262626;
    --ink: #1e1e1e;
    --ink-soft: #4a4a4a;
    --logo-tone: #cfcfcf;
    --tagline-tone: #9a9a9a;
  }
  html, body {
    margin: 0;
    padding: 0;
    width: 1200px;
    height: 900px;
    overflow: hidden;
    background: var(--stage);
  }
  .canvas {
    position: relative;
    width: 1200px;
    height: 900px;
  }
  .card {
    position: absolute;
    left: 290px;
    width: 620px;
    height: 354px;
    border-radius: 22px;
    box-shadow: 0 18px 40px rgba(0,0,0,0.45);
    overflow: hidden;
  }
  .card--front {
    top: 56px;
    background: radial-gradient(ellipse at 60% 40%, #ffffff 0%, var(--card-light) 55%, var(--card-light-edge) 100%);
  }
  .card--back {
    top: 450px;
    background: var(--card-dark);
  }
  .identity {
    position: absolute;
    right: 360px;
    top: 118px;
    text-align: right;
  }
  .identity__name {
    font-family: "Bebas Neue", sans-serif;
    font-size: 46px;
    line-height: 1;
    color: var(--ink);
    letter-spacing: 0.5px;
    margin: 0;
  }
  .identity__role {
    font-family: "Lato", sans-serif;
    font-weight: 300;
    font-size: 15px;
    color: var(--ink-soft);
    margin: 2px 0 0;
  }
  .divider {
    position: absolute;
    left: 280px;
    top: 108px;
    width: 1.5px;
    height: 96px;
    background: var(--ink);
  }
  .contacts {
    position: absolute;
    left: 300px;
    top: 110px;
    margin: 0;
    padding: 0;
    list-style: none;
    font-family: "Lato", sans-serif;
    font-weight: 400;
    font-size: 17px;
    color: var(--ink);
  }
  .contacts__item {
    display: flex;
    align-items: center;
    gap: 10px;
    height: 23px;
  }
  .contacts__icon {
    width: 13px;
    height: 13px;
    flex: none;
  }
  .address {
    position: absolute;
    left: 48px;
    bottom: 58px;
    margin: 0;
    font-family: "Lato", sans-serif;
    font-weight: 400;
    font-size: 17px;
    color: var(--ink-soft);
  }
  .brand {
    position: absolute;
    inset: 0;
    display: flex;
    flex-direction: column;
    align-items: center;
    justify-content: center;
    gap: 22px;
  }
  .brand__lockup {
    display: flex;
    align-items: center;
    gap: 16px;
  }
  .brand__mark {
    width: 26px;
    height: 26px;
    background: var(--logo-tone);
  }
  .brand__name {
    font-family: "Lato", sans-serif;
    font-weight: 300;
    font-size: 40px;
    letter-spacing: 3px;
    color: var(--logo-tone);
    margin: 0;
  }
  .brand__tagline {
    font-family: "Lato", sans-serif;
    font-weight: 300;
    font-size: 15px;
    letter-spacing: 1.5px;
    color: var(--tagline-tone);
    margin: 0;
  }
</style>
</head>
<body>
<main class="canvas">
  <section class="card card--front" aria-label="Card front">
    <div class="identity">
      <h1 class="identity__name">Adrian Cole</h1>
      <p class="identity__role">Director</p>
    </div>
    <div class="divider"></div>
    <ul class="contacts">
      <li class="contacts__item">
        <svg class="contacts__icon" viewBox="0 0 16 16" aria-hidden="true"><path d="M4 1l2.5 3-1.5 2c1 2 3 4 5 5l2-1.5 3 2.5-1.5 2.5C8 16 0 8 1.5 2.5z" fill="#1e1e1e"/></svg>
        <span>+593 7 555-0142</span>
      </li>
      <li class="contacts__item">
        <svg class="contacts__icon" viewBox="0 0 16 16" aria-hidden="true"><rect x="4" y="1" width="8" height="14" rx="1.5" fill="none" stroke="#1e1e1e" stroke-width="1.6"/><circle cx="8" cy="12.5" r="0.9" fill="#1e1e1e"/></svg>
        <span>+593 98 555-0187</span>
      </li>
      <li class="contacts__item">
        <svg class="contacts__icon" viewBox="0 0 16 16" aria-hidden="true"><rect x="1" y="3" width="14" height="10" fill="none" stroke="#1e1e1e" stroke-width="1.5"/><path d="M1 3l7 6 7-6" fill="none" stroke="#1e1e1e" stroke-width="1.5"/></svg>
        <span>BrookvaneConsulting.com</span>
      </li>
      <li class="contacts__item">
        <svg class="contacts__icon" viewBox="0 0 16 16" aria-hidden="true"><circle cx="8" cy="8" r="6.5" fill="none" stroke="#1e1e1e" stroke-width="1.4"/><ellipse cx="8" cy="8" rx="3" ry="6.5" fill="none" stroke="#1e1e1e" stroke-width="1.2"/><path d="M1.5 8h13" stroke="#1e1e1e" stroke-width="1.2"/></svg>
        <span>www.BrookvaneConsulting.com</span>
      </li>
    </ul>
    <p class="address">Calle Laurel y Ribera, Ecuador, EC070415</p>
  </section>

  <section class="card card--back" aria-label="Card back">
    <div class="brand">
      <div class="brand__lockup">
        <span class="brand__mark"></span>
        <p class="brand__name">Brookvane Consulting</p>
      </div>
      <p class="brand__tagline">Inspiration to Dream More, Do More, Become More</p>
    </div>
  </section>
</main>
</body>
</html>
```